Antibacterial Hand Wash Squeeze Tube Label

We're looking for a contemporary label design for a new Antibacterial Hand Wash for an 8oz squeeze tube. The new consumer brand will be sold to consumers in major US retail stores & online. The moisturizing hand wash contains Aloe Vera, vitamin E, and other natural ingredients so the design should include the color green. Real photos are very effective on packaging, so a picture of Aloe Vera or possibly two hands washing would help draw consumers' attention to the tube on the retail shelf. The front label may wrap around the sides. Rear must be left mostly blank
Target Market(s)
US Consumers - retail stores & online
Industry/Entity Type
Consumer

```html
<!DOCTYPE html>
<html lang="en">
<head>
<meta charset="UTF-8">
<title>Hand Wash Tube Label</title>
<link rel="stylesheet" href="https://fonts.googleapis.com/css2?family=Arimo:wght@400;700&display=swap">
<style>
  :root {
    --backdrop: #eef1ee;
    --label-white: #ffffff;
    --brand-green: #3f6f3f;
    --stripe-green: #2e9b5c;
    --copy-green: #4f6a4f;
    --ink: #1c1c1c;
    --aloe-light: #e6f0dc;
    --aloe-mid: #b9d3a4;
    --band-dark: #5d7355;
    --band-light: #8a9c84;
  }
  * { box-sizing: border-box; margin: 0; padding: 0; }
  html, body {
    width: 1200px;
    height: 675px;
    overflow: hidden;
    background: var(--backdrop);
  }
  .canvas {
    position: relative;
    width: 1200px;
    height: 675px;
    display: flex;
    align-items: center;
    justify-content: center;
  }
  .tube-label {
    position: relative;
    width: 280px;
    height: 540px;
    background: var(--label-white);
    font-family: "Arimo", Arial, sans-serif;
    box-shadow: 0 2px 10px rgba(0,0,0,0.08);
    overflow: hidden;
  }
  .label-heading {
    position: absolute;
    top: 62px;
    left: 20px;
  }
  .product-name {
    font-size: 22px;
    font-weight: 700;
    color: var(--brand-green);
    line-height: 1.1;
  }
  .brand-name {
    font-size: 14px;
    font-weight: 700;
    color: var(--ink);
    line-height: 1.2;
    margin-top: 2px;
  }
  .label-stripe {
    position: absolute;
    top: 112px;
    left: 0;
    width: 100%;
    height: 14px;
    background: var(--stripe-green);
  }
  .feature-list {
    position: absolute;
    top: 132px;
    left: 0;
    width: 100%;
    list-style: none;
    text-align: center;
    color: var(--copy-green);
    font-size: 17px;
    line-height: 22px;
  }
  .aloe-photo {
    position: absolute;
    top: 238px;
    left: 0;
    width: 100%;
    height: 162px;
    background: radial-gradient(ellipse at 50% 60%, var(--aloe-mid) 0%, var(--aloe-light) 55%, var(--label-white) 100%);
  }
  .volume-band {
    position: absolute;
    left: 0;
    bottom: 0;
    width: 100%;
    height: 140px;
    background: linear-gradient(180deg, var(--band-light) 0%, var(--band-dark) 18%, var(--band-dark) 82%, var(--band-light) 100%);
    display: flex;
    align-items: center;
    justify-content: center;
  }
  .volume {
    color: #ffffff;
    font-size: 14px;
  }
</style>
</head>
<body>
  <main class="canvas">
    <section class="tube-label">
      <header class="label-heading">
        <h1 class="product-name">Hand Wash</h1>
        <p class="brand-name">Verdelle</p>
      </header>
      <div class="label-stripe"></div>
      <ul class="feature-list">
        <li>Antibacterial</li>
        <li>Moisturizing</li>
        <li>Aloe Vera</li>
        <li>Vitamin E</li>
        <li>Other natural ingredients</li>
      </ul>
      <div class="aloe-photo" role="img" aria-label="Photo of an aloe vera plant with a water splash"></div>
      <div class="volume-band">
        <span class="volume">100ml</span>
      </div>
    </section>
  </main>
</body>
</html>
```